TA BRAMLEY BUSINESS CARD DESIGN PROJECT

We need to utilize our logo that was expertly created on PixelHarbor and now need to match this with a business card design.

```html
<!DOCTYPE html>
<html lang="en">
<head>
<meta charset="utf-8">
<title>TA BRAMLEY Business Card</title>
<link rel="stylesheet" href="https://fonts.googleapis.com/css2?family=Montserrat:wght@500;700&family=Open+Sans:wght@400&display=swap">
<style>
  :root {
    --brand-blue: #1057a8;
    --card-black: #151515;
    --card-white: #ffffff;
    --backdrop: #3a3a3a;
    --text-light: #f2f2f2;
  }
  html, body {
    margin: 0;
    padding: 0;
    width: 1200px;
    height: 900px;
    overflow: hidden;
    background: var(--backdrop);
  }
  .sheet {
    position: relative;
    width: 1200px;
    height: 900px;
  }
  .card {
    position: absolute;
    left: 250px;
    width: 700px;
    height: 400px;
    border-radius: 22px;
    overflow: hidden;
    box-shadow: 0 10px 28px rgba(0,0,0,0.45);
  }
  .card--front {
    top: 35px;
    background: var(--brand-blue);
    display: flex;
    align-items: center;
    justify-content: center;
  }
  .card--back {
    top: 465px;
    background: var(--card-white);
  }
  .wordmark {
    font-family: "Montserrat", sans-serif;
    font-weight: 700;
    letter-spacing: 0.1em;
    margin: 0;
    white-space: nowrap;
  }
  .wordmark--front {
    color: var(--card-white);
    font-size: 74px;
  }
  .wordmark--back {
    position: absolute;
    left: 36px;
    top: 112px;
    color: var(--brand-blue);
    font-size: 40px;
  }
  .back-shape {
    position: absolute;
    inset: 0;
  }
  .contact {
    position: absolute;
    right: 40px;
    top: 96px;
    text-align: right;
    font-family: "Open Sans", sans-serif;
    color: var(--text-light);
  }
  .contact__name {
    font-family: "Montserrat", sans-serif;
    font-weight: 700;
    color: var(--brand-blue);
    font-size: 21px;
    margin: 0;
    white-space: nowrap;
  }
  .contact__role {
    font-size: 17px;
    margin: 2px 0 22px;
  }
  .contact__address {
    font-size: 16px;
    line-height: 1.35;
    margin: 0 0 20px;
  }
  .contact__list {
    list-style: none;
    margin: 0;
    padding: 0;
    font-size: 16px;
    line-height: 1.6;
  }
  .contact__list li {
    display: flex;
    align-items: center;
    justify-content: flex-end;
    gap: 10px;
  }
  .icon {
    width: 14px;
    height: 14px;
    fill: var(--brand-blue);
  }
</style>
</head>
<body>
<main class="sheet">
  <section class="card card--front">
    <h1 class="wordmark wordmark--front">TA BRAMLEY</h1>
  </section>

  <section class="card card--back">
    <svg class="back-shape" width="700" height="400" viewBox="0 0 700 400">
      <path d="M 622 0 C 422 20, 392 110, 372 220 C 352 330, 292 400, 182 400"
            fill="none" stroke="var(--brand-blue)" stroke-width="5"/>
      <path d="M 640 0 C 440 20, 410 110, 390 220 C 370 330, 310 400, 200 400 L 700 400 L 700 0 Z"
            fill="var(--card-black)"/>
    </svg>
    <p class="wordmark wordmark--back">TA BRAMLEY</p>
    <div class="contact">
      <p class="contact__name">DANA WHITFIELD</p>
      <p class="contact__role">Managing Director</p>
      <p class="contact__address">Your address, City<br>State, Zip 1234</p>
      <ul class="contact__list">
        <li>123 456 789
          <svg class="icon" viewBox="0 0 24 24"><path d="M6.6 10.8a15 15 0 0 0 6.6 6.6l2.2-2.2a1 1 0 0 1 1-.25 11.4 11.4 0 0 0 3.6.57 1 1 0 0 1 1 1V20a1 1 0 0 1-1 1A17 17 0 0 1 3 4a1 1 0 0 1 1-1h3.5a1 1 0 0 1 1 1c0 1.25.2 2.45.57 3.57a1 1 0 0 1-.25 1z"/></svg>
        </li>
        <li>info@yourmail.com
          <svg class="icon" viewBox="0 0 24 24"><path d="M2 5h20v14H2z M2 5l10 8 10-8" fill="var(--brand-blue)" stroke="var(--card-black)" stroke-width="1.5"/></svg>
        </li>
        <li>www.yourwebsite.com
          <svg class="icon" viewBox="0 0 24 24"><circle cx="12" cy="12" r="10"/><path d="M2 12h20M12 2c3 3 3 17 0 20M12 2c-3 3-3 17 0 20" fill="none" stroke="var(--card-black)" stroke-width="1.5"/></svg>
        </li>
      </ul>
    </div>
  </section>
</main>
</body>
</html>
```